Build a landing page to promote a service (dialler consultation and support).

We are a call centre consultation firm and we need a landing page to promote a service. The service is Tormalux dialler consultation and support.
If you do not know what Tormalux is, please do some quick "Zorvex" research for more information.
The landing page will be promoted with a paid advertisement, so we want something that is simple, and explains exactly what service we offer.
There are two objectives for the landing page:
1) A "call to action" which directs the user to a contact page, including a form plus all of our contact details.
2) A form for them viewers to enter their details to get a "FREE" quote for their project. This form should be placed on the main page.
Notes:
The call to action will require the viewer to enter their name, email, phone number as well as a description of their request. There will also need to be a drop down menu for the type of quote. This menu should have the following options:
1) Tormalux support
2) Tormalux hosting
3) Tormalux customisation
4) Other
We need 2 pages in total:
1) Main landing page
This is the home page. It will need to clearly indicate our services and our key selling features.
Services:
* Tormalux support
* Tormalux hosting
* Tormalux customisation
Key Selling Features:
* Australian based
* PCI complaint
* 10+ years of dialler and call centre experience
* we run a sister company which is a highly reputable 40 seat call centre, so we know first hand about call centre technology.
The main landing page will have an "about us" section with a few paragraphs about how we got started.
-------------------------------------------------------------------------
2) Contact page
All of our contact details will live on this page, as well as a contact form.
Other notes:
We will be self hosting the landing page.
We already have a domain name.
The design must be clean and incorporate our logo, as well as it's colours. (Logo attached)
We want a fully function HTML landing page, not just a "PSD" design.
The page must be mobile optimised.
Anyone using Tormalux software.

```html
<!DOCTYPE html>
<html lang="en">
<head>
<meta charset="UTF-8">
<title>Kestrelline — Tormalux Support</title>
<link rel="stylesheet" href="https://fonts.googleapis.com/css2?family=Lato:wght@400;700;900&display=swap">
<style>
:root{
  --blue:#1a7fc1;
  --blue-deep:#1b6fb3;
  --teal:#2ab39c;
  --teal-menu:#3bb7a1;
  --ink:#222;
  --text:#555;
  --line:#cfcfcf;
  --footer:#2b2b2b;
  --white:#fff;
}
*{box-sizing:border-box;margin:0;padding:0}
html,body{width:1200px;height:2242px;overflow:hidden}
body{position:relative;font-family:"Lato",sans-serif;color:var(--ink);background:var(--white)}
.abs{position:absolute}

/* header */
.site-header{left:0;top:0;width:1200px;height:133px;background:var(--white)}
.brand{left:75px;top:12px;width:170px;text-align:center}
.brand-dot{width:68px;height:68px;border-radius:50%;background:var(--blue);margin:0 auto 4px}
.brand-name{font-size:31px;font-weight:700;color:var(--blue);letter-spacing:.5px;line-height:1}
.main-nav{top:53px;left:0;font-size:15px;font-weight:700}
.main-nav a{position:absolute;white-space:nowrap;color:var(--ink);text-decoration:none}
.main-nav a.active{color:var(--blue)}
.caret{display:inline-block;margin-left:10px;width:7px;height:7px;border-right:1.6px solid var(--ink);border-bottom:1.6px solid var(--ink);transform:translateY(-3px) rotate(45deg)}
.dropdown{left:782px;top:85px;width:228px;height:138px;background:var(--teal-menu);color:var(--white);font-size:15px;padding-top:15px;z-index:3}
.dropdown::before{content:"";position:absolute;left:44px;top:-7px;border:7px solid transparent;border-top:0;border-bottom-color:var(--teal-menu)}
.dropdown li{list-style:none;height:30.5px;padding-left:51px;position:relative}
.dropdown li::before{content:"»";position:absolute;left:17px;top:-2px;font-size:15px}

/* hero */
.hero{left:0;top:133px;width:1200px;height:582px;background:linear-gradient(110deg,#9aa7b5 0%,#c7b6ae 30%,#a8b3bf 60%,#7f8d9c 100%)}
.hero-notch{left:553px;top:714px;width:96px;height:22px;background:var(--white);clip-path:polygon(0 0,100% 0,50% 100%);background:#a0abb7}
.hero-title{left:75px;top:364px;font-size:49px;font-weight:700;color:var(--white)}
.hero-text{left:76px;top:425px;width:545px;font-size:21.5px;line-height:30px;font-weight:700;color:var(--white)}

/* quote form */
.quote-card{left:704px;top:214px;width:422px;height:442px;background:var(--white);border-radius:9px;box-shadow:0 2px 10px rgba(0,0,0,.18)}
.quote-title{left:19px;top:16px;font-size:32px;font-weight:700;color:var(--blue);white-space:nowrap}
.quote-rule{left:19px;top:62px;width:384px;height:1px;background:#ddd}
.field{left:25px;width:378px;height:40px;border:1px solid var(--line);border-radius:3px;font-size:14px;color:#333;padding:11px 11px}
.field.area{height:76px}
.select-arrows{position:absolute;right:18px;top:12px;width:8px;height:14px}
.quote-btn{left:25px;top:369px;width:378px;height:52px;border-radius:3px;background:linear-gradient(to bottom,#2bb3a3,#1b72b6);color:var(--white);font-size:24px;font-weight:700;text-align:center;line-height:52px}

/* services */
.services{left:0;top:736px;width:1200px;height:379px;background:linear-gradient(to bottom,#fff 0%,#f5f5f5 45%,#ececec 100%)}
.section-title{font-size:43px;font-weight:700;color:var(--blue);white-space:nowrap}
.services .section-title{left:0;width:1200px;text-align:center;top:38px}
.service{top:118px;width:300px;text-align:center}
.service svg{width:72px;height:72px;display:block;margin:0 auto}
.service h3{margin-top:26px;font-size:22px;font-weight:700;color:var(--teal)}
.service p{margin-top:10px;font-size:16.5px;line-height:26px;color:var(--text)}

/* about */
.about-photo{left:601px;top:1175px;width:599px;height:458px;clip-path:polygon(89px 0,100% 0,100% 100%,0 100%);background:linear-gradient(120deg,#d9cfc4 0%,#b9a89a 40%,#8c97a3 80%,#c8ccd0 100%)}
.about .section-title{left:75px;top:1206px}
.about-text{left:75px;top:1278px;width:560px;font-size:17.5px;line-height:26px;color:#333}
.btn{height:53px;line-height:53px;text-align:center;background:linear-gradient(to bottom,#2aa9a5,#1c74b7);color:var(--white);font-size:17px;font-weight:700;letter-spacing:.3px}
.about .btn{left:75px;top:1514px;width:179px}

/* features */
.features-photo{left:0;top:1633px;width:598px;height:457px;clip-path:polygon(0 0,100% 0,505px 100%,0 100%);background:linear-gradient(100deg,#c9cdd2 0%,#e2d6d4 45%,#b7bec6 100%)}
.features .section-title{left:641px;top:1692px}
.feature-list{left:641px;top:1766px;width:470px;list-style:none;font-size:17.5px;line-height:26px;color:#333}
.feature-list li{position:relative;padding-left:34px;margin-bottom:11.5px}
.feature-list svg{position:absolute;left:0;top:6px;width:15px;height:15px}
.features .btn{left:643px;top:1987px;width:179px}

/* footer */
.site-footer{left:0;top:2150px;width:1200px;height:92px;background:var(--footer)}
.copyright{left:75px;top:38px;font-size:12px;color:#d8d8d8}
.social{top:36px;width:20px;height:20px;border-radius:50%;background:#e6e6e6}
</style>
</head>
<body>

<header class="site-header abs">
  <div class="brand abs">
    <div class="brand-dot"></div>
    <div class="brand-name">Kestrelline</div>
  </div>
  <nav class="main-nav abs">
    <a class="active" style="left:617px">HOME</a>
    <a style="left:697px">ABOUT US</a>
    <a style="left:804px">SERVICES<span class="caret"></span></a>
    <a style="left:934px">FEATURES</a>
    <a style="left:1040px">CONTACT US</a>
  </nav>
  <ul class="dropdown abs">
    <li>Tormalux support</li>
    <li>Tormalux hosting</li>
    <li>Tormalux customisation</li>
    <li>Other</li>
  </ul>
</header>

<section class="hero abs" role="img" aria-label="Photo of a smiling call centre agent wearing a headset"></section>
<div class="hero-notch abs"></div>
<h1 class="hero-title abs">Tormalux Support</h1>
<p class="hero-text abs">Praesent arcu mi, consectetur sit amet dignissim et, scelerisque sed lacus. Mauris facilisis mattis lectus, et pellentesque orci ultrices vel.</p>

<form class="quote-card abs">
  <h2 class="quote-title abs">Get A Free Quote Now</h2>
  <div class="quote-rule abs"></div>
  <div class="field abs" style="top:79px">Name</div>
  <div class="field abs" style="top:128px">Email Address</div>
  <div class="field abs" style="top:179px">Phone No</div>
  <div class="field abs" style="top:230px">Select Services
    <svg class="select-arrows" viewBox="0 0 8 14"><path d="M4 0 8 5H0zM4 14 0 9h8z" fill="#222"/></svg>
  </div>
  <div class="field area abs" style="top:278px">Description of their request</div>
  <div class="quote-btn abs">GET A FREE QUOTE</div>
</form>

<section class="services abs">
  <h2 class="section-title abs">Services</h2>
  <div class="service abs" style="left:89px">
    <svg viewBox="0 0 72 72" fill="#222">
      <ellipse cx="30" cy="27" rx="25" ry="18"/>
      <path d="M14 40 8 52 24 43z"/>
      <ellipse cx="46" cy="40" rx="22" ry="16" fill="#fff"/>
      <ellipse cx="46" cy="40" rx="19" ry="13.5"/>
      <path d="M56 50 66 61 52 53z"/>
    </svg>
    <h3>Tormalux Support</h3>
    <p>Aliquam molestie, mi et imperdiet euismod, dui purus auctor tellus, et interdum lacus...</p>
  </div>
  <div class="service abs" style="left:451px">
    <svg viewBox="0 0 72 72" fill="#222">
      <ellipse cx="36" cy="10" rx="28" ry="8"/>
      <path d="M8 16c0 5 12 9 28 9s28-4 28-9v10c0 5-12 9-28 9S8 31 8 26z"/>
      <path d="M8 33c0 5 12 9 28 9s28-4 28-9v10c0 5-12 9-28 9S8 48 8 43z"/>
      <path d="M8 50c0 5 12 9 28 9s28-4 28-9v10c0 5-12 9-28 9S8 65 8 60z"/>
    </svg>
    <h3>Tormalux Hosting</h3>
    <p>Aliquam molestie, mi et imperdiet euismod, dui purus auctor tellus, et interdum lacus...</p>
  </div>
  <div class="service abs" style="left:811px">
    <svg viewBox="0 0 72 72" fill="none" stroke="#222" stroke-width="9">
      <path d="M12 34A24 24 0 0 1 55 20"/>
      <path d="M60 38A24 24 0 0 1 17 52"/>
      <path d="M48 8 66 8 64 28z" fill="#222" stroke="none"/>
      <path d="M24 64 6 64 8 44z" fill="#222" stroke="none"/>
    </svg>
    <h3>Tormalux Customisation</h3>
    <p>Aliquam molestie, mi et imperdiet euismod, dui purus auctor tellus, et interdum lacus...</p>
  </div>
</section>

<section class="about">
  <div class="about-photo abs" role="img" aria-label="Photo of a row of call centre agents working at laptops"></div>
  <h2 class="section-title abs">About Us</h2>
  <p class="about-text abs">Aliquam molestie, mi et imperdiet euismod, dui purus auctor tellus, et interdum lacus lectus et ante.<br>Lorem ipsum dolor sit amet, consectetur adipiscing elit. Donec eu porttitor mauris. Etiam id orci facilisis, venenatis nibh id, condimentum est. Praesent arcu mi, consectetur sit amet dignissim et, scelerisque sed lacus. Mauris facilisis mattis lectus, et pellentesque orci ultrices vel.<br>Donec id elit sollicitudin, commodo urna eget, gravida velit</p>
  <div class="btn abs">READ MORE</div>
</section>

<section class="features">
  <div class="features-photo abs" role="img" aria-label="Photo of a team leader holding a tablet in front of seated call centre agents"></div>
  <h2 class="section-title abs">Key Selling Features</h2>
  <ul class="feature-list abs">
    <li><svg viewBox="0 0 16 16"><circle cx="8" cy="8" r="8" fill="#1a7fc1"/><path d="M4.3 8.3 7 11l4.8-5.2" fill="none" stroke="#fff" stroke-width="2"/></svg>Australian based</li>
    <li><svg viewBox="0 0 16 16"><circle cx="8" cy="8" r="8" fill="#1a7fc1"/><path d="M4.3 8.3 7 11l4.8-5.2" fill="none" stroke="#fff" stroke-width="2"/></svg>PCI complaint</li>
    <li><svg viewBox="0 0 16 16"><circle cx="8" cy="8" r="8" fill="#1a7fc1"/><path d="M4.3 8.3 7 11l4.8-5.2" fill="none" stroke="#fff" stroke-width="2"/></svg>10+ years of dialler and call centre experience</li>
    <li><svg viewBox="0 0 16 16"><circle cx="8" cy="8" r="8" fill="#1a7fc1"/><path d="M4.3 8.3 7 11l4.8-5.2" fill="none" stroke="#fff" stroke-width="2"/></svg>We run a sister company which is a highly reputable<br>40 seat call centre, so we know first hand about call centre technology.</li>
  </ul>
  <div class="btn abs">READ MORE</div>
</section>

<footer class="site-footer abs">
  <p class="copyright abs">Copyright ©2018 Company Name. All Rights Reserved.</p>
  <span class="social abs" style="left:951px" aria-label="Social link"></span>
  <span class="social abs" style="left:987px" aria-label="Social link"></span>
  <span class="social abs" style="left:1026px" aria-label="Social link"></span>
  <span class="social abs" style="left:1066px" aria-label="Social link"></span>
  <span class="social abs" style="left:1105px" aria-label="Social link"></span>
</footer>

</body>
</html>
```